W need a Menu Board designed for a" make your own poke bowl" and Sushi Menu. We would like our logo & Colors to be intergraded with the menu . Also will need to be able to adjust the pricing in the future as needed.

```html
<!DOCTYPE html>
<html lang="en">
<head>
<meta charset="utf-8">
<title>Make Your Own Poke Bowl – Menu Board</title>
<link href="https://fonts.googleapis.com/css2?family=Bebas+Neue&family=Kaushan+Script&family=Lato:ital,wght@0,400;0,900;1,700&display=swap" rel="stylesheet">
<style>
  :root{
    --stage:#a6a6a6;
    --sky:#7ef9fd;
    --sea-mid:#38c3ef;
    --sea-deep:#0a4796;
    --panel-top:#5ab9d9;
    --panel-mid:#1d80cf;
    --panel-deep:#053c8a;
    --navy:#0a3a86;
    --ink:#151515;
    --wood:#4a2a1e;
    --white:#ffffff;
  }
  *{margin:0;padding:0;box-sizing:border-box}
  html,body{width:1200px;height:1200px;overflow:hidden;background:var(--stage)}
  body{position:relative;font-family:'Lato',sans-serif;color:var(--white)}
  .abs{position:absolute}
  ul{list-style:none}
  h1,h2,h3{font-weight:400}

  .board{left:54px;top:214px;width:1092px;height:772px;
    background:linear-gradient(180deg,var(--sky) 0%,var(--sky) 12%,var(--sea-mid) 45%,var(--sea-deep) 100%)}

  .headline{left:97px;top:246px;width:700px;font-family:'Bebas Neue',sans-serif;font-weight:700;
    font-size:82px;line-height:74px;color:var(--ink);white-space:nowrap;
    border-bottom:2px solid var(--ink);letter-spacing:-0.3px}

  .brand{left:862px;top:252px;width:200px;text-align:center;font-family:'Lato',sans-serif;
    font-weight:900;font-size:46px;line-height:60px;color:var(--navy);letter-spacing:2px}

  .panel{border:2.5px solid var(--white);
    background:linear-gradient(180deg,var(--panel-top) 0%,var(--panel-mid) 45%,var(--panel-deep) 100%)}
  .panel--sushi{left:86px;top:352px;width:540px;height:620px}
  .panel--poke{left:646px;top:352px;width:469px;height:620px}

  .plank{background:var(--wood);font-family:'Kaushan Script',cursive;font-size:31px;
    text-align:center;color:var(--white)}
  .plank--sushi{left:284px;top:331px;width:167px;height:55px;line-height:55px}
  .plank--poke{left:797px;top:329px;width:166px;height:56px;line-height:56px}

  .roll-list{left:99px;top:391px;font-size:18.6px;line-height:25.9px}
  .roll-list li{position:relative;width:290px;white-space:nowrap}
  .roll-list .price{position:absolute;left:224px}

  .feature{font-size:19px;line-height:24px}
  .feature .price{position:absolute;left:139px;top:0}
  .feature p{font-size:12.4px;line-height:24.8px;margin-top:2px}
  .feature--house-one{left:411px;top:406px;width:200px}
  .feature--house-two{left:412px;top:593px;width:210px}
  .feature--house-two .price{left:135px}

  .tag{background:var(--navy);border:2px solid var(--white);font-family:'Bebas Neue',sans-serif;
    text-align:center;color:var(--white);white-space:nowrap}
  .tag--negri{left:412px;top:746px;width:121px;height:45px;line-height:45px;font-size:40px;
    background:var(--white);color:var(--navy);border:none;outline:2px solid var(--white)}
  .tag--negri span{display:block;margin:2px;height:41px;line-height:43px;background:var(--white);
    border:2px solid var(--navy)}
  .negri-list{left:418px;top:803px;font-size:19.5px;line-height:24.6px}

  .start{left:700px;top:386px;width:358px;text-align:center;font-style:italic;font-weight:700;
    font-size:21px;line-height:28px}

  .tag--sm{font-size:24px;height:31px;line-height:31px}
  .tag--base{left:677px;top:421px;width:160px}
  .tag--protein{left:669px;top:562px;width:178px}
  .tag--crunch{left:669px;top:720px;width:178px}
  .tag--toppings{left:889px;top:420px;width:177px}
  .tag--premium{left:882px;top:597px;width:177px}
  .tag--sauce{left:907px;top:737px;width:84px}
  .tag--scoop{left:760px;top:870px;width:203px}

  .opts{font-size:15.6px;line-height:18.2px}
  .opts--base{left:679px;top:460px}
  .opts--protein{left:679px;top:598px}
  .opts--crunch{left:679px;top:756px}

  .grid{font-size:15.6px;line-height:19.4px}
  .grid li{position:relative;white-space:nowrap}
  .grid .b{position:absolute;top:0}
  .grid--toppings{left:883px;top:453px}
  .grid--toppings .b{left:101px}
  .grid--toppings .b.in{left:112px}
  .grid--premium{left:877px;top:628px}
  .grid--premium li{line-height:19.6px}
  .grid--premium .b{left:112px}
  .grid--sauce{left:850px;top:768px}
  .grid--sauce .b{left:123px}
  .grid--scoop{left:678px;top:902px;width:400px;line-height:21px}
  .grid--scoop .p1{left:122px}
  .grid--scoop .n2{left:201px}
  .grid--scoop .p2{left:324px}
</style>
</head>
<body>
  <div class="abs board"></div>

  <h1 class="abs headline">MAKE YOUR OWN POKE BOWL</h1>
  <div class="abs brand">TIDEWELL</div>

  <div class="abs panel panel--sushi" role="img" aria-label="Soft underwater blue backdrop with a faint fish silhouette"></div>
  <div class="abs panel panel--poke" role="img" aria-label="Soft underwater blue backdrop"></div>

  <h2 class="abs plank plank--sushi">Sushi Rolls</h2>
  <h2 class="abs plank plank--poke">Poke Bowls</h2>

  <ul class="abs roll-list">
    <li>Tuna Tartar<span class="price">$24.99</span></li>
    <li>Salmon Tartar<span class="price">$22.99</span></li>
    <li>Tuna Tower<span class="price">$16.99</span></li>
    <li>Salmon Tower<span class="price">$16.99</span></li>
    <li>Kani Salad<span class="price">$18.99</span></li>
    <li>Tuna Tataki</li>
    <li>California Roll<span class="price">$9.99</span></li>
    <li>Avocado Roll<span class="price">$7.99</span></li>
    <li>Tuna Roll (Small)<span class="price">$9.99</span></li>
    <li>Salmon Roll (Small)<span class="price">$9.99</span></li>
    <li>Cucumber Roll<span class="price">$7.99</span></li>
    <li>Veggie Roll $9.99</li>
    <li>Salmon Avocado Roll<span class="price">$9.99</span></li>
    <li>Salmon Avocado w/</li>
    <li>Salmon on Top<span class="price">$14.99</span></li>
    <li>Salmon Avocado w/</li>
    <li>Tuna on Top<span class="price">$14.99</span></li>
    <li>Tuna Avocado w/</li>
    <li>Tuna on Top<span class="price">$14.99</span></li>
    <li>Tuna Avocado w/</li>
    <li>Salmon on Top<span class="price">$14.99</span></li>
    <li>Spicy Tuna Roll<span class="price">$9.99</span></li>
  </ul>

  <div class="abs feature feature--house-one">
    Tide Roll<span class="price">$14.99</span>
    <p>(Inside Out w/ Kani,<br>Cucumber, Avocado,<br>&amp; Tempura Flakes<br>Topped w/ Salmon<br>&amp; Dressed with<br>Eel Sauce)</p>
  </div>
  <div class="abs feature feature--house-two">
    Harbor Roll<span class="price">$15.99</span>
    <p>(Inside Out w/ Kani,<br>Cucumber &amp; Cilantro Topped<br>w/ Hamachi, Jalapeno &amp; Dressed<br>w/ Cilantro Truffle Sauce)</p>
  </div>

  <h3 class="abs tag tag--negri"><span>NEGRI</span></h3>
  <ul class="abs negri-list">
    <li>Salmon</li><li>Ahi</li><li>Wahoo</li><li>Hamachi</li><li>Toro</li>
  </ul>

  <p class="abs start">Starting Price $15.99</p>

  <h3 class="abs tag tag--sm tag--base">CHOICE 1 BASE</h3>
  <ul class="abs opts opts--base">
    <li>White Rice</li><li>Brown Rice</li><li>Quinoa</li><li>Zucchini Noodles</li><li>Lettuce</li>
  </ul>

  <h3 class="abs tag tag--sm tag--protein">CHOICE 1 PROTEIN</h3>
  <ul class="abs opts opts--protein">
    <li>Tuna Poke</li><li>Salmon Poke</li><li>Spicy Tuna</li><li>Spicy Salmon</li><li>Kani</li><li>Wahoo</li>
  </ul>

  <h3 class="abs tag tag--sm tag--crunch">CHOICE 1 CRUNCH</h3>
  <ul class="abs opts opts--crunch">
    <li>Tuna Poke</li><li>Salmon Poke</li><li>Spicy Tuna</li><li>Spicy Salmon</li><li>Kani</li><li>Wahoo</li>
  </ul>

  <h3 class="abs tag tag--sm tag--toppings">CHOICE 4 TOPPINGS</h3>
  <ul class="abs grid grid--toppings">
    <li>Asian Slaw<span class="b">Edamame</span></li>
    <li>Red Onion<span class="b">Red Cabbage</span></li>
    <li>Jalapeno<span class="b in">Scallions</span></li>
    <li>Carrot<span class="b in">Radish</span></li>
    <li>Cucumber<span class="b">Tomato</span></li>
    <li>Sprout<span class="b in">Cilantro</span></li>
    <li>Pickled Ginger</li>
  </ul>

  <h3 class="abs tag tag--sm tag--premium">PREMIUM TOPPINGS</h3>
  <ul class="abs grid grid--premium">
    <li>Avocado<span class="b">$2.00</span></li>
    <li>Kani Salad<span class="b">$1.00</span></li>
    <li>Wakame<span class="b">$1.00</span></li>
    <li>Mango<span class="b">$1.00</span></li>
    <li>Pineapple<span class="b">$1.00</span></li>
  </ul>

  <h3 class="abs tag tag--sm tag--sauce">SUACE</h3>
  <ul class="abs grid grid--sauce">
    <li>Spicy Mayo<span class="b">Sweet Chili</span></li>
    <li>Sriracha<span class="b">Ponzu</span></li>
    <li>Eel Sauce<span class="b">Cilantro Garlic Aioli</span></li>
    <li>Basil Aioli<span class="b">Sesame Ginger</span></li>
    <li>Carrot Honey Ginger</li>
  </ul>

  <h3 class="abs tag tag--sm tag--scoop">ADDITIONAL PROTEIN SCOOP</h3>
  <ul class="abs grid grid--scoop">
    <li>Tuna Poke<span class="b p1">$4.00</span><span class="b n2">Salmon Poke</span><span class="b p2">$4.00</span></li>
    <li>Spicy Tuna<span class="b p1">$4.00</span><span class="b n2">Spicy Salmon</span><span class="b p2">$4.00</span></li>
    <li>Kani<span class="b p1">$4.00</span></li>
  </ul>
</body>
</html>
```